Larkmoor Home Works Sales Flyer

We want a sales flyer that outlines our companies strengths with Kitchen & Bath Remodeling. We would like highlight those aspects while also showcasing our ability to do decks and home additions. We want financing packages to be a big part of the flyer.

Target Market(s)

Residential Customers

Requirements
Must have
• Financing options
Highlight Kitchen & bath remodeling
Less subtle is our decks and home additions
Nice to have
• Keep within our logo colors-we are looking for informative flyers that leave homeowners eager to call us after a meeting

```html
<!DOCTYPE html>
<html lang="en">
<head>
<meta charset="utf-8">
<title>Larkmoor Home Works Sales Flyer</title>
<link href="https://fonts.googleapis.com/css2?family=Source+Sans+3:wght@300;400;600;700;800&display=swap" rel="stylesheet">
<style>
:root{
  --page-bg:#dcdcdb;
  --sky:#00b2f2;
  --azure:#0f8fe0;
  --royal:#1a6ad6;
  --navy:#1734a6;
  --heading-blue:#1479d0;
  --text:#3b3b3b;
  --white:#ffffff;
  --panel-a:#ffffff;
  --panel-b:#eeeeee;
}
*{margin:0;padding:0;box-sizing:border-box}
html,body{width:1200px;height:1200px;overflow:hidden;background:var(--page-bg);font-family:"Source Sans 3",sans-serif}
.flyer{position:absolute;left:159px;top:30px;width:1232px;height:1592px;transform:scale(0.7161);transform-origin:0 0;background:var(--white);overflow:hidden;box-shadow:0 0 18px rgba(0,0,0,.25)}
.header{position:absolute;left:0;top:0;width:1232px;height:227px;background:linear-gradient(100deg,var(--sky) 0%,var(--azure) 60%,var(--royal) 100%)}
.brand{position:absolute;left:40px;top:0;width:600px;height:227px;display:flex;align-items:center;justify-content:center;gap:14px;color:var(--white);font-weight:700;font-size:42px;letter-spacing:1px;white-space:nowrap}
.brand-mark{width:22px;height:22px;background:var(--white)}
.cta{position:absolute;right:55px;top:50px;width:320px;text-align:center;color:var(--white)}
.cta-line{font-size:28px;font-weight:400;line-height:38px}
.cta-line strong{font-weight:700}
.cta-phone{display:flex;align-items:center;justify-content:center;gap:10px;font-size:36px;font-weight:700;line-height:44px}
.cta-phone svg{width:18px;height:18px}
.hero{position:absolute;left:0;top:227px;width:1232px;height:529px;overflow:hidden}
.hero-living{position:absolute;inset:0;background:linear-gradient(160deg,#d9dcdc 0%,#a9a59d 40%,#6e6a66 100%);clip-path:polygon(0 0,705px 0,585px 529px,0 529px)}
.hero-bath{position:absolute;inset:0;background:linear-gradient(200deg,#e6e8ea 0%,#a6adb4 45%,#8c8f93 100%);clip-path:polygon(705px 0,1232px 0,1232px 529px,585px 529px)}
.hero-question{position:absolute;left:0;top:184px;width:640px;height:204px;background:rgba(70,130,230,.72);color:var(--white);padding:24px 0 0 78px;font-size:44px;line-height:48px;font-weight:400}
.hero-question strong{font-weight:700}
.hero-title{position:absolute;left:80px;top:412px;color:var(--white);font-size:46px;line-height:46px;font-weight:700;text-shadow:0 2px 6px rgba(0,0,0,.6)}
.hero-rule{position:absolute;left:0;top:756px;width:1232px;height:9px;background:linear-gradient(90deg,var(--azure),var(--royal))}
.service{position:absolute;color:var(--text);overflow:hidden}
.service-top{top:765px;height:348px}
.service-bottom{top:1113px;height:327px}
.col-left{left:0;width:616px;background:linear-gradient(180deg,var(--panel-a),var(--panel-b))}
.col-right{left:616px;width:616px;background:linear-gradient(180deg,var(--panel-b),var(--panel-a))}
.service-bottom.col-left,.service-bottom.col-right{background:var(--white)}
.service-icon{position:absolute;left:34px;top:24px;width:66px;height:70px}
.service-title{position:absolute;left:125px;top:22px;color:var(--heading-blue);font-size:24px;font-weight:600}
.service-intro{position:absolute;left:126px;top:62px;width:470px;font-size:20px;line-height:20.5px;font-weight:400}
.service-list{position:absolute;left:126px;list-style:none;font-size:20px;line-height:22.3px}
.service-list li{position:relative;padding-left:17px}
.service-list li::before{content:"";position:absolute;left:0;top:9px;width:6px;height:6px;background:var(--heading-blue)}
.list-spaced{line-height:24.3px}
.photo{position:absolute}
.photo-bedroom{left:352px;top:131px;width:264px;height:217px;background:linear-gradient(160deg,#d7d2c7,#b7b0a3 50%,#efeeea)}
.photo-shower{left:394px;top:133px;width:222px;height:194px;background:linear-gradient(180deg,#c5c9cd,#8f959b 60%,#d8d6d1)}
.photo-porch{left:352px;top:158px;width:264px;height:169px;background:linear-gradient(180deg,#b3895a 0%,#9fc07f 35%,#5f7f45 70%,#6a4a33 100%)}
.financing{position:absolute;left:0;top:1440px;width:1232px;height:75px;background:linear-gradient(90deg,var(--sky) 0%,var(--azure) 55%,var(--royal) 100%);color:var(--white);display:flex;align-items:center;justify-content:center;gap:28px;white-space:nowrap}
.financing-title{font-size:32px;font-weight:800;letter-spacing:.5px}
.financing-divider{width:2px;height:40px;background:rgba(255,255,255,.6)}
.financing-text{font-size:22px;font-weight:400;line-height:26px}
.financing-text strong{font-weight:700}
.footer{position:absolute;left:0;top:1515px;width:1232px;height:77px;background:linear-gradient(90deg,var(--navy) 0%,#1d4fc0 60%,var(--royal) 100%);border-top:4px solid var(--azure);color:var(--white);font-size:21px;display:flex;align-items:center;justify-content:center}
</style>
</head>
<body>
<main class="flyer">
  <header class="header">
    <div class="brand"><span class="brand-mark"></span>Larkmoor Home Works</div>
    <div class="cta">
      <p class="cta-line">CALL TODAY FOR YOUR</p>
      <p class="cta-line"><strong>FREE</strong> ESTIMATE</p>
      <p class="cta-phone"><svg viewBox="0 0 18 18"><circle cx="9" cy="9" r="9" fill="#e0584a"/><path d="M6 5l2 2-1 1.2a5 5 0 0 0 2.8 2.8L11 10l2 2-1.3 1.3C8.5 13 5 9.5 4.7 6.3z" fill="#fff"/></svg>555-014-2271</p>
    </div>
  </header>

  <section class="hero">
    <div class="hero-living" role="img" aria-label="Photo of a bright open living room with a stone fireplace wall and a marble kitchen island"></div>
    <div class="hero-bath" role="img" aria-label="Photo of a remodeled bathroom with a glass walk-in tile shower and marble vanity"></div>
    <div class="hero-question">Ready for<br>a Beautiful and Functional<br><strong>Kitchen</strong> or <strong>Bathroom</strong>?</div>
    <h1 class="hero-title">WORK WITH A TOP-RATED LOCAL REMODELING<br>COMPANY IN ANKENY, IA</h1>
  </section>
  <div class="hero-rule"></div>

  <section class="service service-top col-left">
    <svg class="service-icon" viewBox="0 0 66 70" fill="none" stroke="#1e5ac8" stroke-width="2.5">
      <path d="M6 16h10M11 10v16M16 18a4 4 0 1 1 0 .1M42 12h14l3 6H39z"/>
      <rect x="3" y="34" width="60" height="30"/><path d="M33 34v30M8 42h20M8 50h20M38 42h20M46 50h6"/>
    </svg>
    <h2 class="service-title">KITCHEN REMODELING</h2>
    <p class="service-intro">Whatever your vision is for your new kitchen, our crew can help you bring it to life. You can trust us for:</p>
    <ul class="service-list" style="top:126px">
      <li>Open concept design services</li>
      <li>Kitchen cabinet installation services</li>
      <li>Kitchen countertop installation services</li>
      <li>Tile installation services</li>
      <li>Lighting installation services</li>
      <li>Plumbing upgrade services</li>
      <li>Electrical upgrade services</li>
      <li>Drywall services</li>
      <li>Painting services</li>
    </ul>
  </section>

  <section class="service service-top col-right">
    <svg class="service-icon" viewBox="0 0 66 70" fill="none" stroke="#1e5ac8" stroke-width="2.5" style="left:26px;top:36px">
      <path d="M4 66h62V38H44V26H30V14H18v10H6v42M18 14h44v24M30 14V4h32v10M38 4v10M46 4v10M54 4v10"/>
    </svg>
    <h2 class="service-title" style="left:132px;top:28px">HOME ADDITIONS</h2>
    <p class="service-intro" style="left:133px;top:64px">No matter what kind of space you need, our team will bring your vision to life. You can hire us if you need a:</p>
    <ul class="service-list list-spaced" style="left:133px;top:127px">
      <li>Bathroom addition</li>
      <li>Bedroom addition</li>
      <li>Garage addition</li>
      <li>Basement addition</li>
      <li>Guest room addition</li>
      <li>Living room addition</li>
      <li>Sunroom addition</li>
    </ul>
    <div class="photo photo-bedroom" role="img" aria-label="Photo of a bright bedroom addition with a white bed and bedside lamps"></div>
  </section>

  <section class="service service-bottom col-left">
    <svg class="service-icon" viewBox="0 0 66 70" fill="none" stroke="#1e5ac8" stroke-width="2.5">
      <circle cx="36" cy="12" r="9"/><path d="M32 16l8-8M14 28h40l-3 8H17zM10 26v-6h6v6M4 36h58v30H4zM14 44h36v12H14zM32 44v12"/>
    </svg>
    <h2 class="service-title">BATHROOM REMODELING</h2>
    <p class="service-intro">When you hire us for your bathroom remodeling project, the possibilities are endless. Our experienced and talented team can:</p>
    <ul class="service-list" style="top:146px;width:265px;line-height:21px">
      <li style="margin-bottom:3px">Install a custom tile shower</li>
      <li style="margin-bottom:3px">Build a new vanity</li>
      <li style="margin-bottom:3px">Install flooring and tile</li>
      <li>Replace your plumbing and light fixtures</li>
    </ul>
    <div class="photo photo-shower" role="img" aria-label="Photo of a glass walk-in tile shower next to a white vanity"></div>
  </section>

  <section class="service service-bottom col-right">
    <svg class="service-icon" viewBox="0 0 66 70" fill="none" stroke="#1e5ac8" stroke-width="2.5" style="left:30px;top:28px">
      <path d="M6 22a28 18 0 0 1 56 0zM20 22a14 18 0 0 1 28 0M34 4v56M6 50h56v6H6zM12 56v8M56 56v8M44 50l14-14M40 44l10 6"/>
    </svg>
    <h2 class="service-title" style="left:134px">DECKS/PATIOS</h2>
    <p class="service-intro" style="left:134px">An outdoor space is a great addition to any residential property. When you decide to build a patio or deck, you'll be able to experience a variety of benefits. Your outdoor area will increase your:</p>
    <ul class="service-list" style="left:134px;top:169px;width:190px;line-height:21px">
      <li style="margin-bottom:3px">Property value</li>
      <li style="margin-bottom:3px">Curb appeal</li>
      <li>Functional living space</li>
    </ul>
    <div class="photo photo-porch" role="img" aria-label="Photo of a screened porch with a wooden ceiling, dining table and a view of green trees"></div>
  </section>

  <section class="financing">
    <h2 class="financing-title">FINANCING OPTIONS AVAILABLE</h2>
    <span class="financing-divider"></span>
    <p class="financing-text">Flexible <strong>monthly payment plans</strong> for kitchens, baths,<br>decks and additions. Ask us during your free estimate!</p>
  </section>

  <footer class="footer">www.larkmoorhome.com</footer>
</main>
</body>
</html>
```